Expedition Cruise Sales Website for the Polar Regions (Antarctica & Arctic)

This will be a website for selling cruises.
This site should have a homepage, a ship page, destinations, and itineraries.
I have created a file specifying each page, and it is attached.
Pages:
1. Home
2. Cruise Lines
- 2.1 Ships
3. Destinations
- 3.1 Region - 3.2 Country - 3.3 City
4. Itineraries
- 4.1 Itinerary
5. Blog / Travel Tips 6. About Us
7. Contact
Please take a look on the attached pdf
Target Market(s)
Expedition Travelers
Coding
Coded - Design and coding required
Number of Pages Required
5+ page
Font styles to use
Look and feel
Each slider illustrates characteristics of the customer's brand and the style your logo design should communicate.

```html
<!DOCTYPE html>
<html lang="en">
<head>
<meta charset="utf-8">
<title>Polarvia – Antarctica Cruises & Expeditions</title>
<link rel="stylesheet" href="https://fonts.googleapis.com/css2?family=Poppins:wght@400;500;700&family=Roboto:wght@400;500;700&display=swap">
<style>
:root{
  --navy:#16223d;
  --navy-deep:#121c33;
  --blue:#2a5ba8;
  --blue-dark:#1f4c92;
  --ink:#1c1c1c;
  --muted:#555;
  --line:#d8dde6;
  --quote:#c9ccd1;
  --green:#4cc34a;
}
*{box-sizing:border-box;margin:0;padding:0}
html,body{width:1200px;height:4706px;overflow:hidden}
body{position:relative;font-family:'Roboto',sans-serif;color:var(--ink);background:#fff}
.abs{position:absolute}
.h2{font-family:'Poppins',sans-serif;font-size:38px;font-weight:400;color:var(--ink);text-align:center;left:0;width:1200px}
.h2 b{font-weight:700}
.rule{width:74px;height:4px;background:var(--blue);left:563px}
.btn{display:flex;align-items:center;justify-content:center;color:#fff;font-weight:700;font-size:15px;border-radius:3px}
.btn-blue{background:var(--blue)}
.btn-navy{background:var(--navy)}
.ph{border-radius:2px}

/* top bar */
.topbar{top:0;left:0;width:1200px;height:33px;background:var(--navy);color:#fff;font-size:13px;z-index:5}
.topbar span{position:absolute;top:9px;display:flex;align-items:center;gap:6px}
.soc-dot{width:16px;height:16px;border-radius:50%;background:#2d3a58;top:9px}

/* nav */
.nav{top:33px;left:0;width:1200px;height:77px;background:#fff;z-index:5}
.nav a{position:absolute;top:30px;font-size:14px;font-weight:500;color:var(--ink);text-decoration:none}
.nav a.active{color:var(--blue)}
.tab{top:100px;left:480px;width:240px;height:66px;background:#fff;clip-path:polygon(0 0,100% 0,88% 100%,12% 100%);z-index:6}
.brand-mark{left:576px;top:50px;width:48px;height:48px;border-radius:50%;background:var(--blue);z-index:7}
.brand{left:480px;top:114px;width:240px;text-align:center;font-family:'Poppins',sans-serif;font-weight:500;font-size:32px;line-height:40px;color:var(--blue);z-index:7}

/* hero */
.hero{top:110px;left:0;width:1200px;height:748px;background:linear-gradient(180deg,#86a9d4 0%,#c4d7ec 10%,#e7eff8 22%,#b5cbe3 33%,#8aa9cf 40%,#3b5c88 46%,#1f3556 50%,#4d6f9c 54%,#c9d9ea 59%,#eef3f9 66%,#d2deea 76%,#e9eff6 88%,#f7f9fc 100%)}
.hero h1{font-family:'Poppins',sans-serif;font-size:44px;font-weight:400;color:var(--navy-deep);top:88px;left:0;width:1200px;text-align:center}
.hero h1 b{font-weight:700}
.search{left:168px;width:864px;height:64px;background:#fff;border-radius:6px;box-shadow:0 4px 16px rgba(0,0,0,.15)}
.field{top:14px;width:220px;height:38px;border:1px solid var(--line);border-radius:4px;font-size:13px;color:#555;padding:11px 12px;display:flex;justify-content:space-between}

/* deals */
.card{width:308px;height:470px;border:1px solid var(--line);background:#fff;top:1046px}
.card .img{position:absolute;left:6px;top:6px;width:294px;height:236px;background:linear-gradient(180deg,#3e6eae 0%,#9fbddd 40%,#e4edf6 55%,#2b4f82 75%,#5d82b4 100%)}
.card .price{position:absolute;left:14px;top:208px;color:#fff;font-size:14px}
.card .price b{font-size:17px}
.card h3{position:absolute;left:18px;top:262px;font-size:16px;font-weight:700}
.card .meta{position:absolute;left:18px;top:294px;font-size:12.5px;color:#444}
.card p{position:absolute;left:18px;top:342px;width:270px;font-size:12.5px;line-height:20px;color:#666}
.card .btn{position:absolute;top:405px;width:130px;height:40px;font-size:14px}
.arrow{top:1262px;width:24px;height:40px}

/* destinations */
.dest{top:1939px;width:231px;height:291px}
.dest-label{top:2250px;width:231px;text-align:center;font-size:17px;font-weight:700}

/* cruise lines */
.cl-band{top:2465px;left:0;width:1200px;height:411px;background:linear-gradient(180deg,#0e1a34,#1a2b50)}
.cl-img{top:2640px;width:468px;height:305px;background:linear-gradient(180deg,#8fb0d6 0%,#dfe8f3 35%,#3d6aa6 60%,#1d3b6e 100%)}
.cl-box{top:2894px;width:414px;height:196px;background:#fff;box-shadow:0 2px 10px rgba(0,0,0,.12);text-align:center}
.cl-box .logo{position:absolute;left:157px;top:-50px;width:100px;height:100px;border-radius:50%;background:#fff;box-shadow:0 2px 8px rgba(0,0,0,.15)}
.cl-box .logo i{position:absolute;left:30px;top:30px;width:40px;height:40px;border-radius:50%;background:var(--navy)}
.cl-box h3{position:absolute;top:70px;width:100%;font-size:18px;font-weight:500}
.cl-box p{position:absolute;top:108px;left:20px;width:374px;font-size:13px;line-height:21px;color:#555}
.cl-box .btn{position:absolute;top:174px;left:104px;width:202px;height:44px;font-size:14px}

/* testimonials */
.quote{top:3292px;z-index:2}
.tcard{top:3314px;width:300px;height:262px;background:#fff;border:1px solid var(--line);box-shadow:6px 6px 0 -1px #fff,7px 7px 0 0 var(--blue)}
.tcard p{position:absolute;left:36px;top:60px;width:228px;font-size:13.5px;line-height:24px;color:#555;text-align:justify}
.tcard .av{position:absolute;left:36px;top:172px;width:56px;height:56px;border-radius:50%;background:linear-gradient(180deg,#a9c2e0,#3a5f93)}
.tcard .nm{position:absolute;left:106px;top:180px;font-size:16px;font-weight:700}
.tcard .rg{position:absolute;left:106px;top:206px;font-size:13px;color:#888}

/* newsletter */
.news{top:4026px;left:0;width:1200px;height:302px;background:var(--blue)}
.news h2{font-family:'Poppins',sans-serif;font-size:38px;color:#fff;font-weight:400;top:64px;width:1200px;text-align:center}
.news h2 b{font-weight:700}

/* footer */
.footer{top:4328px;left:0;width:1200px;height:378px;background:var(--navy)}
.footer h4{font-size:16px;font-weight:700;color:#fff;top:80px}
.flist{top:116px;font-size:13px;color:#d8deea;line-height:26px}
</style>
</head>
<body>

<div class="abs topbar">
  <span style="left:112px"><svg width="12" height="12" viewBox="0 0 24 24"><path fill="#fff" d="M6.6 10.8a15 15 0 006.6 6.6l2.2-2.2c.3-.3.7-.4 1-.2 1.1.4 2.3.6 3.6.6.6 0 1 .4 1 1V20c0 .6-.4 1-1 1A17 17 0 013 4c0-.6.4-1 1-1h3.5c.6 0 1 .4 1 1 0 1.3.2 2.5.6 3.6.1.3 0 .7-.2 1z"/></svg>+1 (555) 014 2200</span>
  <span style="left:283px"><svg width="13" height="12" viewBox="0 0 24 24"><path fill="none" stroke="#fff" stroke-width="2" d="M3 5h18v14H3zM3 5l9 7 9-7"/></svg>info@polarvia.com</span>
  <i class="abs soc-dot" style="left:1017px"></i>
  <i class="abs soc-dot" style="left:1043px"></i>
  <i class="abs soc-dot" style="left:1069px"></i>
</div>

<nav class="abs nav">
  <a class="active" style="left:111px">Home</a>
  <a style="left:175px">Cruise Lines</a>
  <a style="left:283px">Destinations</a>
  <a style="left:393px">Itineraries</a>
  <a style="left:748px">Blog</a>
  <a style="left:802px">About Us</a>
  <a style="left:888px">Contact</a>
  <div class="abs btn btn-blue" style="left:965px;top:19px;width:125px;height:40px;font-size:14px">Book Now</div>
</nav>
<div class="abs tab"></div>
<div class="abs brand-mark"></div>
<div class="abs brand">Polarvia</div>

<section class="abs hero" role="img" aria-label="Cruise ship sailing among Antarctic icebergs with polar bears and penguins on the ice">
  <h1 class="abs"><b>Antarctica Cruises</b> &amp; Expeditions</h1>
  <div class="abs" style="top:150px;left:0;width:1200px;text-align:center;font-size:16px;font-weight:500;color:#111">Explore breathtaking destinations, luxury accommodations, and unforgettable experiences.</div>
  <div class="abs" style="left:505px;top:208px;width:44px;height:44px;border-radius:50%;background:#fff"></div>
  <svg class="abs" style="left:521px;top:222px" width="14" height="16"><path d="M0 0L14 8L0 16z" fill="#111"/></svg>
  <div class="abs" style="left:569px;top:222px;font-size:13px;font-weight:700;color:#111">WATCH THE VIDEO</div>
  <div class="abs search" style="top:447px">
    <div class="abs field" style="left:12px">📍 Destination<span>⌄</span></div>
    <div class="abs field" style="left:244px">Date<span>⌄</span></div>
    <div class="abs field" style="left:476px">Cruise Line<span>⌄</span></div>
    <div class="abs btn btn-blue" style="left:714px;top:14px;width:138px;height:38px;font-size:14px">⌕&nbsp; Explore</div>
  </div>
</section>

<h2 class="abs h2" style="top:936px"><b>Exclusive Cruise</b> Deals &amp; Offers</h2>
<div class="abs rule" style="top:996px"></div>
<svg class="abs arrow" style="left:48px" viewBox="0 0 24 40"><path d="M18 4L4 20l14 16" fill="none" stroke="#888" stroke-width="4"/></svg>
<svg class="abs arrow" style="left:1132px" viewBox="0 0 24 40"><path d="M6 4l14 16L6 36" fill="none" stroke="#888" stroke-width="4"/></svg>

<div class="abs card" style="left:110px">
  <div class="img ph" role="img" aria-label="Expedition cruise ship beside icebergs"></div>
  <div class="price">From &nbsp;<b>$ 12,235</b></div>
  <h3>Best Antarctic Cruises</h3>
  <div class="meta">◷ 9-24 Days, 8 Itineraries &nbsp;&nbsp;&nbsp; 199 Guests</div>
  <p>Lorem ipsum dolor consectetur adipiscing eiusmod labore dolore magna aliqua.</p>
  <div class="btn btn-navy" style="left:18px">View Details</div>
  <div class="btn btn-blue" style="left:156px">Book Now</div>
</div>
<div class="abs card" style="left:446px">
  <div class="img ph" role="img" aria-label="Expedition ship in front of snowy mountains"></div>
  <div class="price">From &nbsp;<b>$ 12,235</b></div>
  <h3>Best Antarctic Cruises</h3>
  <div class="meta">◷ 9-24 Days, 8 Itineraries &nbsp;&nbsp;&nbsp; 199 Guests</div>
  <p>Lorem ipsum dolor consectetur adipiscing eiusmod labore dolore magna aliqua.</p>
  <div class="btn btn-navy" style="left:18px">View Details</div>
  <div class="btn btn-blue" style="left:156px">Book Now</div>
</div>
<div class="abs card" style="left:782px">
  <div class="img ph" role="img" aria-label="Cruise ship reflected in calm polar water"></div>
  <div class="price">From &nbsp;<b>$ 12,235</b></div>
  <h3>Best Antarctic Cruises</h3>
  <div class="meta">◷ 9-24 Days, 8 Itineraries &nbsp;&nbsp;&nbsp; 199 Guests</div>
  <p>Lorem ipsum dolor consectetur adipiscing eiusmod labore dolore magna aliqua.</p>
  <div class="btn btn-navy" style="left:18px">View Details</div>
  <div class="btn btn-blue" style="left:156px">Book Now</div>
</div>

<div class="abs" role="img" aria-label="Snowy mountain range with penguins standing on the right" style="top:1552px;left:0;width:1200px;height:340px;background:linear-gradient(180deg,#fff 0%,#eef2f7 14%,#c3d0df 26%,#8fa4bd 36%,#b7c6d8 46%,#dfe7f0 58%,#f1f5f9 74%,#fff 100%)"></div>

<h2 class="abs h2" style="top:1824px"><b>Highlighted</b> Destinations</h2>
<div class="abs rule" style="top:1882px"></div>
<div class="abs dest ph" style="left:111px;background:linear-gradient(180deg,#7fa6d3,#d8e6f3 45%,#9b3a34 58%,#3a6aa0 72%,#2a5585)" role="img" aria-label="Red research hut below Antarctic glacier"></div>
<div class="abs dest ph" style="left:360px;background:linear-gradient(180deg,#6f93bf,#a9bfd8 25%,#3d5a4a 45%,#2a4060 60%,#1d3b62)" role="img" aria-label="Cape Horn rocky island in open sea"></div>
<div class="abs dest ph" style="left:608px;background:linear-gradient(180deg,#7fa3cc,#b8cbe0 25%,#8a8a6a 42%,#b7a27a 55%,#1f5f8a 70%,#174b70)" role="img" aria-label="Colourful coastal town in the Falklands"></div>
<div class="abs dest ph" style="left:856px;background:linear-gradient(180deg,#8aa4c4,#dfe6ee 35%,#8c949e 55%,#cfd7df 70%,#5b5f66)" role="img" aria-label="Penguins on a South Georgia beach"></div>
<div class="abs dest-label" style="left:111px">Antarctica</div>
<div class="abs dest-label" style="left:360px">Cape Horn</div>
<div class="abs dest-label" style="left:608px">The Falklands</div>
<div class="abs dest-label" style="left:856px">South Georgia</div>
<div class="abs btn btn-blue" style="left:484px;top:2325px;width:230px;height:49px;font-size:16px">View All Destinations</div>

<div class="abs cl-band" role="img" aria-label="Dark night-sea band with a penguin and a small yacht decoration"></div>
<h2 class="abs h2" style="top:2524px;color:#fff"><b>Cruise Line</b> Highlights</h2>
<div class="abs rule" style="top:2582px"></div>
<svg class="abs" style="left:0;top:2800px" width="22" height="40"><path d="M18 4L4 20l14 16" fill="none" stroke="#fff" stroke-width="4"/></svg>
<svg class="abs" style="left:1132px;top:2800px" width="24" height="40"><path d="M6 4l14 16L6 36" fill="none" stroke="#fff" stroke-width="4"/></svg>
<div class="abs cl-img ph" style="left:111px" role="img" aria-label="Expedition yacht beside glaciers"></div>
<div class="abs cl-img ph" style="left:621px" role="img" aria-label="Cruise ship sailing through ice floes"></div>
<div class="abs cl-box" style="left:139px">
  <div class="logo"><i></i></div>
  <h3>Glacierline Cruises</h3>
  <p>Lorem ipsum dolor sit amet, consectetur adipiscing elit, incididunt ut labore et dolore magna aliqua.</p>
  <div class="btn btn-blue">See Glacierline Cruises</div>
</div>
<div class="abs cl-box" style="left:648px">
  <div class="logo"><i></i></div>
  <h3>Northwind Cruises</h3>
  <p>Lorem ipsum dolor sit amet, consectetur adipiscing elit, incididunt ut labore et dolore magna aliqua.</p>
  <div class="btn btn-blue">See Northwind Cruises</div>
</div>

<h2 class="abs h2" style="top:3186px"><b>Customer</b> Testimonials</h2>
<div class="abs rule" style="top:3244px"></div>

<div class="abs tcard" style="left:97px">
  <p>The Mediterranean cruise was a dream! Exceptional service and breathtaking sights consectetur sed do eiusmod tempor incididunt.</p>
  <div class="av" role="img" aria-label="Customer photo"></div>
  <div class="nm">Mara Lindqvist</div><div class="rg">Antarctica</div>
</div>
<div class="abs tcard" style="left:444px">
  <p>The Mediterranean cruise was a dream! Exceptional service and breathtaking sights consectetur sed do eiusmod tempor incididunt.</p>
  <div class="av" role="img" aria-label="Customer photo"></div>
  <div class="nm">Mara Lindqvist</div><div class="rg">Antarctica</div>
</div>
<div class="abs tcard" style="left:789px">
  <p>The Mediterranean cruise was a dream! Exceptional service and breathtaking sights consectetur sed do eiusmod tempor incididunt.</p>
  <div class="av" role="img" aria-label="Customer photo"></div>
  <div class="nm">Mara Lindqvist</div><div class="rg">Antarctica</div>
</div>
<svg class="abs quote" style="left:134px" width="80" height="50" viewBox="0 0 80 50"><g fill="#c9ccd1"><circle cx="16" cy="34" r="15"/><path d="M2 33C2 16 12 5 28 2l2 7C20 12 15 19 15 27z"/><circle cx="56" cy="34" r="15"/><path d="M42 33C42 16 52 5 68 2l2 7C60 12 55 19 55 27z"/></g></svg>
<svg class="abs quote" style="left:481px" width="80" height="50" viewBox="0 0 80 50"><g fill="#c9ccd1"><circle cx="16" cy="34" r="15"/><path d="M2 33C2 16 12 5 28 2l2 7C20 12 15 19 15 27z"/><circle cx="56" cy="34" r="15"/><path d="M42 33C42 16 52 5 68 2l2 7C60 12 55 19 55 27z"/></g></svg>
<svg class="abs quote" style="left:826px" width="80" height="50" viewBox="0 0 80 50"><g fill="#c9ccd1"><circle cx="16" cy="34" r="15"/><path d="M2 33C2 16 12 5 28 2l2 7C20 12 15 19 15 27z"/><circle cx="56" cy="34" r="15"/><path d="M42 33C42 16 52 5 68 2l2 7C60 12 55 19 55 27z"/></g></svg>

<div class="abs" role="img" aria-label="Polar bears, penguins and a cruise ship on an icy shore" style="top:3615px;left:0;width:1200px;height:411px;background:linear-gradient(180deg,#fff 0%,#e7eef6 14%,#bccfe4 28%,#8eaacd 38%,#36557f 45%,#4f719d 50%,#d7e3ef 56%,#f2f6fa 66%,#c9d6e4 80%,#e8eef5 90%,#9fb4cc 100%)"></div>

<section class="abs news">
  <h2 class="abs"><b>Stay Updated on the</b> Best Cruise Deals</h2>
  <div class="abs" style="top:129px;width:1200px;text-align:center;font-size:13px;color:#fff">Sign up for exclusive discounts, travel tips, and insider news.</div>
  <div class="abs" style="left:263px;top:183px;width:398px;height:46px;background:#fff;border-radius:3px;font-size:13px;color:#777;padding:15px 12px">Email Address</div>
  <div class="abs btn btn-navy" style="left:672px;top:183px;width:184px;height:46px;font-size:13px">Subscribe Now</div>
  <div class="abs" style="left:893px;top:184px;width:44px;height:44px;border-radius:50%;background:var(--green)"></div>
</section>

<footer class="abs footer">
  <div class="abs" style="left:218px;top:80px;width:44px;height:44px;border-radius:50%;background:#fff"></div>
  <div class="abs" style="left:100px;top:140px;width:280px;text-align:center;font-family:'Poppins',sans-serif;font-weight:500;font-size:40px;color:#fff">Polarvia</div>
  <div class="abs" style="left:142px;top:226px;width:36px;height:36px;border-radius:50%;background:#fff"></div>
  <div class="abs" style="left:196px;top:226px;width:36px;height:36px;border-radius:50%;background:#fff"></div>
  <div class="abs" style="left:248px;top:226px;width:36px;height:36px;border-radius:50%;background:#fff"></div>
  <div class="abs" style="left:302px;top:226px;width:36px;height:36px;border-radius:50%;background:#fff"></div>

  <h4 class="abs" style="left:442px">Quick Links</h4>
  <div class="abs flist" style="left:442px">Home<br>Cruise Lines<br>Destinations<br>Itineraries<br>Blog<br>About Us</div>
  <h4 class="abs" style="left:614px">About Company</h4>
  <div class="abs flist" style="left:614px">FAQ<br>Privacy Policy<br>Contact<br>Terms &amp; Conditions<br>Sitemap</div>
  <h4 class="abs" style="left:807px">Contact Us</h4>
  <svg class="abs" style="left:805px;top:120px" width="13" height="13" viewBox="0 0 24 24"><path fill="#fff" d="M6.6 10.8a15 15 0 006.6 6.6l2.2-2.2c.3-.3.7-.4 1-.2 1.1.4 2.3.6 3.6.6.6 0 1 .4 1 1V20c0 .6-.4 1-1 1A17 17 0 013 4c0-.6.4-1 1-1h3.5c.6 0 1 .4 1 1 0 1.3.2 2.5.6 3.6.1.3 0 .7-.2 1z"/></svg>
  <div class="abs" style="left:838px;top:118px;font-size:13px;color:#fff;font-weight:700">Phone</div>
  <div class="abs" style="left:838px;top:140px;font-size:13px;color:#d8deea">555-014-2200</div>
  <svg class="abs" style="left:803px;top:180px" width="15" height="12" viewBox="0 0 24 20"><path fill="#fff" d="M0 0h24v20H0zM2 2l10 8 10-8"/></svg>
  <div class="abs" style="left:838px;top:176px;font-size:13px;color:#fff;font-weight:700">Email</div>
  <div class="abs" style="left:838px;top:198px;font-size:13px;color:#d8deea">info@polarvia.com</div>
  <svg class="abs" style="left:806px;top:240px" width="10" height="14" viewBox="0 0 10 14"><path fill="#fff" d="M5 0a5 5 0 015 5c0 4-5 9-5 9S0 9 0 5a5 5 0 015-5zm0 3a2 2 0 100 4 2 2 0 000-4z"/></svg>
  <div class="abs" style="left:838px;top:236px;font-size:13px;color:#fff;font-weight:700">Location</div>
  <div class="abs" style="left:838px;top:258px;font-size:13px;color:#d8deea">210 Harbor Lane, Portland, USA</div>
  <div class="abs" style="left:1125px;top:267px;width:32px;height:32px;border-radius:50%;background:var(--blue)"></div>
  <svg class="abs" style="left:1134px;top:277px" width="14" height="10"><path d="M1 9l6-7 6 7" fill="none" stroke="#fff" stroke-width="2.5"/></svg>
  <div class="abs" style="left:0;top:336px;width:1200px;text-align:center;font-size:13px;color:#d8deea">2025 Copyright - polarvia | All Rights Reserved</div>
</footer>

</body>
</html>
```